Business Card for a mobile physiotherapy company

I need a layout for a business card for a mobile physiotherapy company.
Slogan is "Mobile Physiotherapy - Your Road To Recovery"
Phone number is 867-555-0142
Email VardenTherapy@postnest.ca (subject to change with website)
Website www.VardenTherapy.ca
My name and credentials: Luke Varden Luke Varden, BSc(kin), MPT, CAFCI, IMS
Information maybe included: Direct Billing, Services including Physiotherapy, IMS, acupuncture
Maybe include facebook and instagram logos
One side with the logo clean and sharp
Other side with details, try not to look too busy, keep everything concise

```html
<!DOCTYPE html>
<html lang="en">
<head>
<meta charset="utf-8">
<title>Varden Therapy – Business Card</title>
<link href="https://fonts.googleapis.com/css2?family=Open+Sans:wght@400;600;700&family=Tinos:wght@700&display=swap" rel="stylesheet">
<style>
  :root {
    --navy: #2c4871;
    --forest: #0b5449;
    --white: #ffffff;
    --ink: #1d1d1f;
    --rule: #b9bcbf;
    --stage-light: #e6e7e8;
    --stage-dark: #b4b6b9;
  }
  * { box-sizing: border-box; margin: 0; padding: 0; }
  html, body { width: 1200px; height: 1113px; overflow: hidden; }
  body {
    position: relative;
    background: linear-gradient(90deg, var(--stage-light) 0%, var(--stage-dark) 100%);
    font-family: "Open Sans", Arial, sans-serif;
  }
  .card {
    position: absolute;
    width: 768px;
    height: 438px;
    border-radius: 40px;
    overflow: hidden;
  }
  .card--front {
    left: 334px; top: 83px;
    background: var(--white);
    border: 1px solid #2a2a2a;
  }
  .card--back {
    left: 90px; top: 593px;
    background: var(--forest);
  }

  .header-band {
    position: absolute; left: 0; top: 0; width: 100%; height: 106px;
    background: var(--navy);
    border-bottom: 6px solid var(--white);
    box-shadow: 0 6px 0 var(--forest);
  }

  .holder { position: absolute; right: 38px; top: 32px; text-align: right; color: var(--white); }
  .holder__name { font-family: "Tinos", "Times New Roman", serif; font-weight: 700; font-size: 26px; letter-spacing: 1px; line-height: 1; }
  .holder__creds { font-size: 15px; margin-top: 12px; }

  .brand {
    position: absolute; left: 40px; top: 186px;
    display: flex; align-items: center; gap: 12px;
    font-family: "Open Sans", Arial, sans-serif; font-weight: 700; color: var(--forest);
  }
  .brand__mark { width: 22px; height: 22px; background: var(--forest); flex: none; }
  .brand__name { font-size: 32px; line-height: 1; }

  .contacts { position: absolute; left: 39px; top: 309px; list-style: none; }
  .contacts li { display: flex; align-items: center; gap: 6px; height: 33px; font-size: 18px; color: var(--ink); }
  .contacts svg { width: 18px; height: 18px; flex: none; }

  .divider { position: absolute; left: 339px; top: 318px; width: 1px; height: 86px; background: var(--rule); }

  .services { position: absolute; left: 369px; top: 310px; color: var(--forest); }
  .services__title { font-size: 18px; font-weight: 700; color: var(--navy); margin-bottom: 8px; }
  .services__list { list-style: none; display: grid; grid-template-columns: auto auto; column-gap: 14px; row-gap: 2px; font-size: 18px; }

  .slogan {
    position: absolute; left: 0; right: 0; top: 264px; text-align: center;
    font-family: "Tinos", "Times New Roman", serif; font-weight: 700; font-size: 27px; color: var(--white);
  }
</style>
</head>
<body>

<section class="card card--front" aria-label="Card front">
  <div class="header-band"></div>

  <div class="holder">
    <p class="holder__name">LUKE VARDEN</p>
    <p class="holder__creds">BSc(kin), MPT, CAFCI, IMS</p>
  </div>

  <div class="brand">
    <span class="brand__mark"></span>
    <p class="brand__name">Varden Therapy</p>
  </div>

  <ul class="contacts">
    <li>
      <svg viewBox="0 0 20 20" aria-hidden="true"><circle cx="10" cy="10" r="8.5" fill="none" stroke="var(--navy)" stroke-width="1.6"/><path d="M7 5.5l1.6 2.2-1 1.2c.6 1.3 1.6 2.3 2.9 2.9l1.2-1 2.2 1.6-.9 1.6c-3.6-.4-6.6-3.4-7-7z" fill="var(--navy)"/></svg>
      867-555-0142
    </li>
    <li>
      <svg viewBox="0 0 20 20" aria-hidden="true"><circle cx="10" cy="10" r="8.5" fill="none" stroke="var(--navy)" stroke-width="1.6"/><rect x="5.5" y="7" width="9" height="6.5" fill="var(--navy)"/><path d="M5.5 7l4.5 3.5L14.5 7" fill="none" stroke="var(--white)" stroke-width="1"/></svg>
      VardenTherapy@postnest.ca
    </li>
    <li>
      <svg viewBox="0 0 20 20" aria-hidden="true"><g fill="none" stroke="var(--navy)" stroke-width="1.4"><circle cx="10" cy="10" r="8"/><ellipse cx="10" cy="10" rx="3.5" ry="8"/><path d="M2 10h16M3.5 6h13M3.5 14h13"/></g></svg>
      www.VardenTherapy.ca
    </li>
  </ul>

  <div class="divider"></div>

  <div class="services">
    <p class="services__title">Services Including</p>
    <ul class="services__list">
      <li>• Physiotherapy</li>
      <li>• Direct Billing</li>
      <li>• Ims</li>
      <li>• Acupuncture</li>
    </ul>
  </div>
</section>

<section class="card card--back" aria-label="Card back">
  <p class="slogan">Mobile Physiotherapy - Your Road To Recovery</p>
</section>

</body>
</html>
```